Talvoro Web Design

We need a redesign of our current website www.talvoro-example.com

THIS IS A DESIGN STAGE ONLY

We have attached details of the whole project for your understanding only

We do not want to change our Logo but do want to have a more modern and intuitive feel to the site.

The first stage is the design but we are also looking for a coder to take the site to the next level

Talvoro has a current website that has been in operation for the past 6 years the design was based around the Saas self-service model and while functional does not meet Talvoro needs with regard to the new positioning.

We are happy to stay in Joomla or will look at alternatives

The purpose of the redesign is to align the look and feel of the website to meet our current new brand position and to provide a access point for the delivery of new content from Blogs and white papers as well as a portal for information for our current users for gathering Tips and Tricks and access to additional resources to assist them to provide feedback and get support.

Talvoro is Australia's only PPM (Project and Portfolio Management) software provider that caters to the needs of project managers and C-level executives looking for insights into the alignment of resources to business strategy and investment decisions.

As companies gain maturity in PPM there is a need for innovation and management of change beyond just implementation of tools this is why Talvoro has evolved from being a SaaS to becoming a SwS (Software with Service) provider.

Talvoro is recognized as the tool of choice amongst program and project managers that is able to provide the user with an intuitive reliable interface that is capable of evolving and maturing to meet and exceed client requirements.

We are able to provide people at the coalface with tools that enable them to manage resources, scope, time sheeting, issues, changes and risk with excellent reporting functionality.

For C-level executives we are able to provide Business Intelligence (BI) functionality and reporting by integrating the PPM data with other business management systems such as ERP and CRM to provide a insight beyond pure PPM reporting.

We are able to provide Project Management insights from years of experience working with our clients in developing solutions that are inline with the evolution that comes with change.

Please feel free to email me on marcus.hale@talvoro-example.com if you require any further details. A Site map and a wire frame is available.

Competitor sites include

www.plenvix-example.com
www.corbelo-example.com
www.quandrit-example.com
www.vestrel-example.com
Updates

Hi All 

We are getting some great designs coming in and really appreciate all of your efforts.

Some feedback to you all is that we have a preference for cleaner designs that take into account comprehension ability. So reverse type to us looks good but doesnt always get the cut through.

We have to remember that this is a marketing site first and foremost so what we are looking for is the ability to engage with our audience and get them to start to explore. That is upto us to provide great content and what we want from the design is the ability to be be able to engage with our Audience.

For your consideration please review this info from our marketing plan

There are 3 main communication groups inthe sales process.

Users-        These are the peoplewho will be at the coal face inputting the data and using the product on adaily basis. It is key to provide them with an easy to use and functional toolthat is able to provide them with the information they are looking for easily andintuitively. They have the capacity to say yes and can push the sale decisionup the chain. They equally have the power to say No and stop the sales processin its tracks. They will have a opinion who or what they feel is the best ofbreed and will try to influence the process.

Users are split into two groups.

Group1- They will be diploma if not degree qualifiedwill be a mix of Male and female with majority aged 18 to 35 they are at thecareer development stage of their life cycle normally on an income 45k to 70kper annum. We would position these people very strongly in the “What is in itfor me”.

Group2- PM who has used a variety of tools and systemsover the years they will be pre disposed to one or more systems and has morethan likely been exposed to MSP. Usually in the 30 to 50 year old age rangewith extensive on the job experience.

KeyInfluencers- These are the people who while notactually utilizing the software need to receive information in the form ofreports etc from the system. They normally don’t have the capacity to say yesbut they most certainly can say no. They will have come from a PM or IT roleand have a strong understanding of the PM processes. Influencers will be 30 to50 years of age they are at the family development stage with strong demandsfrom work and family predominantly male but not exclusively. They would bedegree qualified and possibly have completed or looking at additional studies. Therewill be an emphasis on getting the job done right. They are very time poor and hardto communicate with and engage. While being time poor they have an affinitywith and understand the greater good.

DecisionMakers- These are our key decision makers whilethey may not have direct input into the system or processes they are at the endof the day the people who approve the expenditure.

There is a huge demand for this person’stime with a multitude of people from internal employees and management,suppliers, customers, the community and potential suppliers. They are oftentravelling and going from one subject matter to another meeting after meeting.They will be at the stage where children are gaining some independents or leftthe home, career is stabilized and a clear path is formed. They are very directand deal in the facts and figures when it comes to decision making, they arenormally highly educated to the MBA or Doctorate level. They will be driven byoutcomes not the process of getting there.

 

A consistent theme across this group isthe following.

Psychographics

·Values time and considers ittheir single most limited resource.

·Excited about accepting andusing innovative ideas and products always wants to be at the fore front.

·Value adding has priority overprice

·Consistent web users: preferinternet over magazines and newspapers

Behavior

·They are leaders in productselection and respond to the opinions of the ‘Industry Experts’ when makingpurchase decisions.

·This group will look to theinternet to acquire the information

·Will make an informed decisionto purchase after due consideration.

·This group can be a powerfulsales force resulting from the referral network they build and use

Hope this helps

Hi All

Sorry for the delay we are in the final stages of decisions, so sorry we have had people away from the office who need to be involved in the process.

We will submit individual questions to those in the running and let all of the people who didnt get through this time as to why shortly.

We would like to thank you all for your efforts and submissions.

Regards

Marcus Hale 

Industry/Entity Type

Business Management

Requirements
Must have
• The scope of the website is to provide a modern functional website that is easy to navigate and provides a range of products and services to meet the needs of our potential clients and current users.

Two potential groups of viewers exist:
1. Potential Clients and users from the Project management community these would be split into 3 distinct groups. ( Please refer to Page 20 Talvoro marketing Plan)
a. Project Managers
b. Project Directors
c. Business Managers
2. Current Talvoro Users

The goal of website is to engage with the project management community reinforcing the Talvoro Brand as Software with Service the key ethos should be around the company being thought leaders and industry experts with a strong commitment to clients and the success of their Portfolio/Program Management Office

Maintaining a modern and user friendly site is of the highest importance in order to hold users attention and guide the viewer to information that will lead to a decision to pursue accreditation and association with the Talvoro Brand

We would like to guide potential clients to want to engage with us in assisting them to understand their current position in the P3M3 maturity model and to use us as a source for information and guidance.

Benefits for using the site should include:
• Information from a broad spectrum of Project Management professionals and recognized industry experts.
• Information on the Talvoro Product and Services
• Timely and up to date information that encourages readers to return to the site
• Call to action, and plans for potential users of Talvoro software.
• Demonstrate the benefits of accreditation and Call to action for current users to gain accreditation.
• Call to action for attending monthly webinars
• Ability to review past webinars, whitepapers etc.

```html
<!DOCTYPE html>
<html lang="en">
<head>
<meta charset="utf-8">
<title>Talvoro</title>
<link rel="stylesheet" href="https://fonts.googleapis.com/css2?family=Bebas+Neue&family=Arimo:ital,wght@0,400;0,700;1,400&family=PT+Sans+Narrow&display=swap">
<style>
:root{
  --page:#ebebeb;
  --topbar:#efefef;
  --dark:#1d1d1d;
  --white:#ffffff;
  --ink:#1a1a1a;
  --body:#3c3c3c;
  --muted:#8a8a8a;
  --card:#f3f3f3;
  --gear:#9a9a9a;
  --band:rgba(60,60,66,.82);
  --sq1:#3fa9dc;
  --sq2:#c8322b;
  --sq3:#3b5a9a;
}
*{margin:0;padding:0;box-sizing:border-box}
html,body{width:1062px;height:1200px;overflow:hidden}
body{position:relative;background:var(--page);font-family:"Arimo",Arial,sans-serif;color:var(--body)}
a{color:inherit;text-decoration:none}

.topbar{position:absolute;left:0;top:0;width:1062px;height:29px;background:var(--topbar)}
.topbar nav{position:absolute;right:90px;top:8px;font-size:11px;color:var(--ink);display:flex;gap:10px}
.topbar nav .gap{margin-left:6px}

.header{position:absolute;left:0;top:29px;width:1062px;height:81px;background:var(--dark)}
.brand{position:absolute;left:98px;top:20px;color:var(--white);font-size:36px;font-weight:700;line-height:1;letter-spacing:-.5px}
.mainnav{position:absolute;right:90px;top:43px;display:flex;gap:34px;font-family:"PT Sans Narrow",sans-serif;font-size:15px;color:var(--white)}

.hero{position:absolute;left:87px;top:119px;width:884px;height:389px;background:linear-gradient(100deg,#c9d8e2 0%,#b7a9ae 30%,#8a6f66 55%,#c1b0a8 75%,#d9cfc6 100%)}
.hero .dots{position:absolute;right:23px;top:31px;display:flex;gap:3px}
.hero .dots span{width:10px;height:8px;background:rgba(255,255,255,.75)}
.hero .band{position:absolute;left:0;bottom:0;width:884px;height:56px;background:var(--band);font-family:"Bebas Neue",sans-serif;font-size:17px;color:var(--white)}
.hero .band span{position:absolute;top:19px}

.section-title{position:absolute;left:0;width:1062px;text-align:center;font-family:"Bebas Neue",sans-serif;font-weight:400;color:var(--ink);letter-spacing:2px}

.card{position:absolute;top:597px;width:210px;height:221px;background:var(--card)}
.card .icon{position:absolute;left:70px;top:-25px;width:69px;height:69px;border-radius:50%;background:var(--white)}
.card .icon svg{position:absolute;left:18px;top:18px}
.card h3{position:absolute;left:0;top:62px;width:210px;text-align:center;font-family:"Bebas Neue",sans-serif;font-weight:400;font-size:17px;color:var(--ink)}
.card p{position:absolute;left:14px;top:100px;width:182px;text-align:center;font-size:11.5px;line-height:14px;color:var(--body)}
.card .more{position:absolute;left:91px;top:182px;width:28px;height:28px;border-radius:50%;background:var(--white);font-size:11px;color:var(--ink);text-align:center;line-height:27px}

.block-title{position:absolute;top:884px;font-family:"Bebas Neue",sans-serif;font-weight:400;font-size:23px;color:var(--ink)}
.avatar{position:absolute;left:117px;top:934px;width:58px;height:41px;background:linear-gradient(180deg,#d8d8d8,#6f6f6f)}
.quote{position:absolute;left:189px;top:932px;width:450px;font-size:14px;font-style:italic;line-height:17px;color:var(--muted)}
.cite{position:absolute;left:114px;top:997px;font-size:12px;color:var(--muted);letter-spacing:.5px}

.client{position:absolute;display:flex;align-items:center;gap:6px;font-size:20px;font-weight:700;color:var(--ink)}
.client i{display:block;width:14px;height:14px}

.footer{position:absolute;left:0;top:1053px;width:1062px;height:147px;background:var(--dark);color:var(--white);font-size:12px}
.footer ul{position:absolute;list-style:none}
.footer li{height:19.5px}
.footer .copy{position:absolute;left:117px;top:121px}
.footer .x5{position:absolute;left:832px;top:35px}
.footer .social{position:absolute;left:863px;top:28px;display:flex;gap:6px}
.footer .social span{width:28px;height:28px;border-radius:4px}
</style>
</head>
<body>

<div class="topbar">
  <nav>
    <a href="#">Home FAQ</a><a href="#">Download</a><a class="gap" href="#">Support &amp; Training</a><a href="#">Customers</a><a href="#">About Us</a><a class="gap" href="#">Login</a><a href="#">Contact Us</a>
  </nav>
</div>

<header class="header">
  <div class="brand">Talvoro</div>
  <nav class="mainnav">
    <a href="#">HOME</a><a href="#">FEATURES</a><a href="#">PRICING</a><a href="#">SIGN UP</a>
  </nav>
</header>

<section class="hero" role="img" aria-label="Photo of a team working together at a whiteboard">
  <div class="dots"><span></span><span></span><span></span><span></span><span></span></div>
  <div class="band">
    <span style="left:27px">PROJECT MANAGEMENT</span>
    <span style="left:258px">TIMESHEET SOFTWARE</span>
    <span style="left:498px">RESOURCE MANAGEMENT</span>
    <span style="left:751px">ISSUE MANAGEMENT</span>
  </div>
</section>

<h2 class="section-title" style="top:524px;font-size:24px">FEATURES &amp; BENEFITS</h2>

<svg width="0" height="0" style="position:absolute">
  <defs>
    <symbol id="gear" viewBox="0 0 34 34">
      <g fill="var(--gear)">
        <circle cx="17" cy="17" r="11"/>
        <rect x="14" y="1" width="6" height="8" rx="1"/>
        <rect x="14" y="25" width="6" height="8" rx="1"/>
        <rect x="1" y="14" width="8" height="6" rx="1"/>
        <rect x="25" y="14" width="8" height="6" rx="1"/>
        <rect x="14" y="1" width="6" height="8" rx="1" transform="rotate(45 17 17)"/>
        <rect x="14" y="25" width="6" height="8" rx="1" transform="rotate(45 17 17)"/>
        <rect x="1" y="14" width="8" height="6" rx="1" transform="rotate(45 17 17)"/>
        <rect x="25" y="14" width="8" height="6" rx="1" transform="rotate(45 17 17)"/>
      </g>
      <circle cx="17" cy="17" r="5" fill="#fff"/>
    </symbol>
  </defs>
</svg>

<article class="card" style="left:96px">
  <div class="icon"><svg width="34" height="34"><use href="#gear"/></svg></div>
  <h3>PROJECT MANAGEMENT</h3>
  <p>Sui blanditiistes es prae tiuptatum delenitimat qudolores etres quamoles tiasexceuri sintsuincupaqui.</p>
  <a class="more" href="#">»</a>
</article>
<article class="card" style="left:315px">
  <div class="icon"><svg width="34" height="34"><use href="#gear"/></svg></div>
  <h3>TIMESHEET SOFTWARE</h3>
  <p>Sui blanditiistes es prae tiuptatum delenitimat qudolores etres quamoles tiasexceuri sintsuincupaqui.</p>
  <a class="more" href="#">»</a>
</article>
<article class="card" style="left:533px">
  <div class="icon"><svg width="34" height="34"><use href="#gear"/></svg></div>
  <h3>RESOURCE MANAGEMENT</h3>
  <p>Sui blanditiistes es prae tiuptatum delenitimat qudolores etres quamoles tiasexceuri sintsuincupaqui.</p>
  <a class="more" href="#">»</a>
</article>
<article class="card" style="left:752px">
  <div class="icon"><svg width="34" height="34"><use href="#gear"/></svg></div>
  <h3>ISSUE MANAGEMENT</h3>
  <p>Sui blanditiistes es prae tiuptatum delenitimat qudolores etres quamoles tiasexceuri sintsuincupaqui.</p>
  <a class="more" href="#">»</a>
</article>

<h2 class="block-title" style="left:114px">WHAT DO THEY SAY?</h2>
<div class="avatar" role="img" aria-label="Portrait photo of the quoted client"></div>
<blockquote class="quote">“ Atum delenitimos atquq udolorese etres quamo lestiasexceuri sintum piditaprdentimilique suincu.paqui officia deserunt mollianimid estlaborum et dolorum massafugharum ”</blockquote>
<div class="cite">CEO, OSTREVA</div>

<h2 class="block-title" style="left:689px">CUSTOMERS</h2>
<div class="client" style="left:688px;top:924px"><i style="background:#d8281f"></i>Fernhaul</div>
<div class="client" style="left:820px;top:924px"><i style="background:var(--ink)"></i>Quorex</div>
<div class="client" style="left:684px;top:983px"><i style="background:#f0a020"></i>Dravlo</div>

<footer class="footer">
  <ul style="left:118px;top:30px">
    <li>Home</li><li>FAQ</li><li>Support &amp; Training</li><li>Contact Us</li>
  </ul>
  <ul style="left:267px;top:30px">
    <li style="height:22px">Tour</li><li style="height:22px">Features</li><li style="height:22px">Pricing</li><li>Sign up</li>
  </ul>
  <ul style="left:391px;top:27px">
    <li style="height:22px">Careers</li><li style="height:22px">Privacy Policy</li><li style="height:22px">Terms of Sale</li><li>Sitemap</li>
  </ul>
  <div class="x5">X5</div>
  <div class="social">
    <span style="background:var(--sq1)" role="img" aria-label="Social link"></span>
    <span style="background:var(--sq2)" role="img" aria-label="Video channel link"></span>
    <span style="background:var(--sq3)" role="img" aria-label="Social page link"></span>
  </div>
  <div class="copy">Copyrights 2013. All rights reserved</div>
</footer>

</body>
</html>
```